Business Card Design Project

use presentation folder design and my logo and make 4 over 4 business cards

Industry/Entity Type

Business

Requirements
Must have
• use the design from my presentation folder and put my logo on it

Name
Title
phone
fax
email

```html
<!DOCTYPE html>
<html lang="en">
<head>
<meta charset="utf-8">
<title>Kindpath Counseling – Business Card</title>
<link rel="stylesheet" href="https://fonts.googleapis.com/css2?family=Exo+2:wght@400;500&display=swap">
<style>
  :root{
    --page:#e6e4e2;
    --slate:#7d7976;
    --slate-dark:#6d6966;
    --sand:#d8c4b5;
    --sand-light:#f2e7de;
    --white:#ffffff;
    --brown:#8b5d3f;
    --ink:#3b3633;
    --figure:#c5ae9d;
  }
  *{margin:0;padding:0;box-sizing:border-box}
  html,body{width:1200px;height:1000px;overflow:hidden;background:var(--page);font-family:"Exo 2",sans-serif}
  .canvas{position:relative;width:1200px;height:1000px}
  .card{position:absolute;width:525px;height:300px;overflow:hidden;box-shadow:0 8px 22px rgba(0,0,0,.18)}
  .card-back{left:45px;top:250px}
  .card-front{left:630px;top:450px}
  .card-bg{position:absolute;inset:0;width:100%;height:100%}

  .brand{position:absolute;display:flex;align-items:center;gap:10px}
  .brand-mark{width:34px;height:34px;border-radius:50%;flex:none}
  .brand-text{display:flex;flex-direction:column;line-height:1}
  .brand-name{font-size:30px;font-weight:500}
  .brand-sub{font-size:10px;letter-spacing:3px;margin-top:3px}
  .brand-tag{font-size:10px;margin-top:3px}

  .card-back .brand{left:95px;top:110px;color:var(--white)}
  .card-back .brand-mark{background:var(--white)}
  .card-front .brand{right:22px;top:28px;color:var(--brown)}
  .card-front .brand-mark{background:var(--brown)}
  .card-front .brand-name{font-size:26px}

  .figure-art{position:absolute;left:30px;top:20px;width:150px;height:230px;border-radius:60px 10px 80px 10px;background:linear-gradient(160deg,var(--figure),rgba(197,174,157,0));opacity:.7}

  .holder{position:absolute;left:148px;top:120px}
  .holder-name{font-size:29px;font-weight:500;color:var(--white);letter-spacing:1px}
  .holder-title{font-size:17px;color:var(--ink);margin:2px 0 0 34px}

  .contact{position:absolute;left:40px;bottom:22px;list-style:none;font-size:15px;color:var(--ink);line-height:1.3}
  .contact-label{color:var(--brown);font-weight:500;margin-right:6px}
</style>
</head>
<body>
<main class="canvas">

  <section class="card card-back" aria-label="Business card back">
    <svg class="card-bg" viewBox="0 0 525 300" preserveAspectRatio="none">
      <rect width="525" height="300" fill="var(--slate)"/>
      <polygon points="525,70 525,300 300,300" fill="var(--sand-light)"/>
      <polygon points="525,40 525,62 290,300 265,300" fill="var(--white)"/>
    </svg>
    <div class="brand">
      <span class="brand-mark"></span>
      <div class="brand-text">
        <span class="brand-name">Kindpath</span>
        <span class="brand-sub">COUNSELING</span>
        <span class="brand-tag">a proactive recovery center</span>
      </div>
    </div>
  </section>

  <section class="card card-front" aria-label="Business card front">
    <svg class="card-bg" viewBox="0 0 525 300" preserveAspectRatio="none">
      <rect width="525" height="300" fill="var(--sand)"/>
      <path d="M305,0 C390,40 470,130 525,230 L525,0 Z" fill="var(--sand-light)"/>
      <path d="M300,0 C385,40 465,130 525,236" fill="none" stroke="var(--white)" stroke-width="6"/>
    </svg>
    <div class="figure-art" role="img" aria-label="Faint stylised figure decoration"></div>
    <div class="brand">
      <span class="brand-mark"></span>
      <div class="brand-text">
        <span class="brand-name">Kindpath</span>
        <span class="brand-sub">COUNSELING</span>
        <span class="brand-tag">a proactive recovery center</span>
      </div>
    </div>
    <div class="holder">
      <p class="holder-name">Elena Varga</p>
      <p class="holder-title">markering manager</p>
    </div>
    <ul class="contact">
      <li><span class="contact-label">[P]</span>+11 500 317</li>
      <li><span class="contact-label">[F]</span>+11 500 482731</li>
      <li><span class="contact-label">[E]</span>example@example.com</li>
    </ul>
  </section>

</main>
</body>
</html>
```